Business Card Design

New business card design

Target Market(s)

Residential & Commercial Property Managers

Industry/Entity Type

Plumbing Services

Contact Information for Business Card

Name - Rowan Keddle, title - Director, Phone Number - 0431 286 517, email - rowan@tbk-plumbing.com.au, Company ABN - 73 215 904 386,

Font styles to use
Sans Serif

Colors
0054AA
0677BA
7BADD7
CADEEF
E8F1F8

```html
<!DOCTYPE html>
<html lang="en">
<head>
<meta charset="utf-8">
<title>TBK Plumbing Services – Business Card</title>
<link rel="stylesheet" href="https://fonts.googleapis.com/css2?family=Montserrat:wght@400;500;700&display=swap">
<style>
  :root {
    --page-bg: #e9e6e1;
    --brand-blue: #2aa7e0;
    --ink: #1f2833;
    --muted: #6b6b6b;
    --card-white: #ffffff;
  }
  * { box-sizing: border-box; margin: 0; padding: 0; }
  html, body { width: 1200px; height: 931px; overflow: hidden; }
  body {
    background: var(--page-bg);
    font-family: "Montserrat", sans-serif;
    color: var(--ink);
    position: relative;
  }
  .card {
    position: absolute;
    width: 580px;
    height: 332px;
    border-radius: 22px;
    overflow: hidden;
    box-shadow: 0 10px 26px rgba(0,0,0,0.22);
  }
  .card-front { left: 60px; top: 70px; background: var(--brand-blue); }
  .card-back { left: 560px; top: 530px; background: var(--card-white); }

  .wordmark {
    font-weight: 500;
    color: var(--ink);
    display: flex;
    align-items: center;
    gap: 12px;
    white-space: nowrap;
  }
  .wordmark-dot {
    width: 14px; height: 14px; border-radius: 50%;
    background: var(--card-white);
  }
  .card-front .wordmark {
    position: absolute; left: 0; right: 0; top: 145px;
    justify-content: center; font-size: 34px; letter-spacing: 1px;
  }
  .card-back .wordmark {
    position: absolute; right: 34px; top: 34px;
    font-size: 19px; letter-spacing: 0.5px;
  }
  .card-back .wordmark-dot { background: var(--brand-blue); width: 10px; height: 10px; }

  .rule-main {
    position: absolute; left: 34px; right: 34px; top: 92px;
    height: 1.5px; background: var(--ink);
  }
  .person { position: absolute; left: 34px; top: 112px; }
  .person-name { font-weight: 700; font-size: 25px; }
  .person-title { font-weight: 400; font-size: 15px; margin-top: 2px; }
  .rule-short { width: 170px; height: 1.5px; background: var(--ink); margin-top: 8px; }

  .contacts { position: absolute; left: 34px; top: 196px; list-style: none; }
  .contacts li {
    display: flex; align-items: center; gap: 10px;
    font-size: 14px; line-height: 23px;
  }
  .contacts svg { width: 15px; height: 15px; flex: none; }
  .abn-label { color: var(--brand-blue); font-weight: 700; }

  .address {
    position: absolute; right: 34px; top: 210px;
    text-align: right; font-size: 13px; line-height: 18px;
  }
  .band {
    position: absolute; left: 0; right: 0; bottom: 0; height: 16px;
    background: var(--brand-blue);
  }
</style>
</head>
<body>
  <section class="card card-front" aria-label="Card front">
    <div class="wordmark"><span class="wordmark-dot"></span>TBK Plumbing Services</div>
  </section>

  <section class="card card-back" aria-label="Card back">
    <div class="wordmark"><span class="wordmark-dot"></span>TBK Plumbing Services</div>
    <div class="rule-main"></div>

    <div class="person">
      <div class="person-name">Rowan Keddle</div>
      <div class="person-title">Director</div>
      <div class="rule-short"></div>
    </div>

    <ul class="contacts">
      <li>
        <svg viewBox="0 0 24 24" aria-hidden="true"><path fill="#2aa7e0" d="M6.6 10.8a15 15 0 0 0 6.6 6.6l2.2-2.2a1 1 0 0 1 1-.25 11.4 11.4 0 0 0 3.6.57 1 1 0 0 1 1 1V20a1 1 0 0 1-1 1A17 17 0 0 1 3 4a1 1 0 0 1 1-1h3.5a1 1 0 0 1 1 1c0 1.25.2 2.45.57 3.57a1 1 0 0 1-.25 1z"/></svg>
        0431 286 517
      </li>
      <li>
        <svg viewBox="0 0 24 24" aria-hidden="true"><path fill="#2aa7e0" d="M3 5h18a1 1 0 0 1 1 1v12a1 1 0 0 1-1 1H3a1 1 0 0 1-1-1V6a1 1 0 0 1 1-1zm9 7.5L20 7H4z"/></svg>
        rowan@tbk-plumbing.com.au
      </li>
      <li>
        <svg viewBox="0 0 24 24" aria-hidden="true"><circle cx="12" cy="12" r="10" fill="#2aa7e0"/><path d="M2 12h20M12 2c3 3 3 17 0 20M12 2c-3 3-3 17 0 20" stroke="#fff" stroke-width="1.4" fill="none"/></svg>
        www.tbk-plumbing.com.au
      </li>
      <li><span><span class="abn-label">ABN</span> - 73 215 904 386</span></li>
    </ul>

    <div class="address">48 Harbour Reach Road<br>Kirrawee, NSW 2232</div>
    <div class="band"></div>
  </section>
</body>
</html>
```